Luxury Real Estate Website, Midwest, United States

We need web design services for a luxury website. We need IDX Integration with our MLS. We want this to be a very simple website with amazing graphics. We want it to link up with our MailChimp account in order to generate leads through a "More Information" Pop up on the main page. We want the main page to be covered with one large graphic that is a rolling slideshow of active listings of $400,000 and up from the IDX Integration. We need this website to give a very exclusive and sleek look. Lots of black is good... I will upload our logos in Black and Silver. We will also need an "About" page that we are going to call "Qeno Info". We want our graphics to be extremely impressive. Keep in mind, we are a company in the Midwest of the United States, and our real estate has a different look than homes in California or Florida. We need graphics that are realistic for the Midwest, yet still high-end.
Target Market(s)
Luxury Homeowners in the Midwest United States. The graphics needs to be pristine.
Industry/Entity Type
Real Estate
Coding
Coded - Design and coding required
Number of Pages Required
3 page
Requirements
Must have
- Large graphics with IDX Integration. The photos of real estate need to represent real estate that is common in the Midwest, United States. We also need MailChimp integration. We need a pop up that is titled "My Free Market Analysis" that makes them fill out a contact form asking for Full Name, Email Address, Phone Number and Address. This needs to be a pop up on the front page and will integrate with our MailChimp account. We also need a page called "About Qe No Home". And another page where clients can download informational PDFs. The main component needs to be a front page search engine connected with the IDX to access active listings from our MLS. I attached our logos and a sample front page of a website. I would love for ours to look similar.
Nice to have
- Lake House photos on midwest lakes are a plus.
Should not have
- Should not have clutter. This website needs to be clean, luxurious and exclusive.

```html
<!DOCTYPE html>
<html lang="en">
<head>
<meta charset="utf-8">
<title>Harbor Crest Realty</title>
<link rel="stylesheet" href="https://fonts.googleapis.com/css2?family=Roboto:wght@400;500;700&family=Open+Sans:ital,wght@0,400;0,600;1,400&display=swap">
<style>
:root{
  --ink:#1d1d1d;
  --text:#5e5e5e;
  --muted:#8a8a8a;
  --ghost:#e9e9ec;
  --accent:#c6d3e6;
  --accent-text:#2b3445;
  --footer:#262626;
  --footer-text:#b9b9b9;
  --white:#ffffff;
  --line:#3a3a3a;
}
*{box-sizing:border-box;margin:0;padding:0}
html,body{width:1200px;height:3243px;overflow:hidden}
body{position:relative;background:var(--white);font-family:"Open Sans",Arial,sans-serif;color:var(--text)}
.abs{position:absolute}

/* header */
.site-header{left:0;top:0;width:1200px;height:93px;background:var(--white)}
.brand{left:100px;top:28px;display:flex;align-items:center;gap:10px;font-family:"Roboto",Arial,sans-serif;font-weight:500;font-size:24px;color:var(--ink);letter-spacing:1px}
.brand-mark{width:14px;height:14px;background:var(--ink)}
.main-nav{right:100px;top:36px;display:flex;gap:30px;font-size:13px;font-weight:600;color:var(--ink)}

/* hero */
.hero{left:0;top:93px;width:1200px;height:507px;background:linear-gradient(180deg,#d8e4ec 0%,#b9a68f 18%,#8f7a63 40%,#a89a78 55%,#4f7d33 70%,#6c9a3c 88%,#6d8fa3 100%)}
.hero-title{left:0;top:276px;width:1200px;text-align:center;font-family:"Roboto",Arial,sans-serif;font-weight:700;font-size:44px;color:var(--white);text-shadow:0 2px 6px rgba(0,0,0,.35)}
.search-input{left:292px;top:360px;width:436px;height:48px;background:var(--white);font-size:12px;font-style:italic;color:var(--muted);padding:15px 18px}
.search-btn{left:746px;top:360px;width:161px;height:48px;background:var(--accent);color:var(--accent-text);font-family:"Roboto",Arial,sans-serif;font-weight:500;font-size:16px;letter-spacing:1.5px;text-align:center;line-height:48px}

/* section ghosts */
.ghost-title{font-family:"Roboto",Arial,sans-serif;font-weight:700;color:var(--ghost);line-height:1;white-space:nowrap}

/* about */
.photo{box-shadow:0 2px 6px rgba(0,0,0,.18)}
.about-main{left:152px;top:710px;width:380px;height:533px;background:linear-gradient(180deg,#3f76c2 0%,#8db3de 38%,#c9c3b7 55%,#a39d93 70%,#5c8a31 88%,#4a7a26 100%)}
.about-title{left:558px;top:700px;font-size:102px}
.about-copy{left:563px;top:805px;width:487px;font-size:13px;line-height:23px;text-align:justify;color:var(--muted)}
.read-more{left:563px;top:953px;width:127px;height:40px;background:var(--accent);color:var(--accent-text);font-size:13px;letter-spacing:1px;text-align:center;line-height:40px}
.about-small-1{left:563px;top:1025px;width:228px;height:218px;background:linear-gradient(160deg,#4f7fb8 0%,#3a6a3a 45%,#b35a2a 75%,#7b3b1d 100%)}
.about-small-2{left:820px;top:1025px;width:228px;height:218px;background:linear-gradient(180deg,#5d8f4a 0%,#2f5d2b 45%,#8c7a4a 70%,#4e5a3a 100%)}

/* features */
.features-title{left:95px;top:1435px;font-size:102px}
.features-photo{left:640px;top:1354px;width:460px;height:260px;background:linear-gradient(180deg,#6d8f62 0%,#2f4f2a 40%,#3b3f3e 60%,#4f8a31 82%,#6b6a5a 100%)}
.feature{width:300px;text-align:center}
.feature svg{display:block;margin:0 auto}
.feature h3{margin-top:16px;font-family:"Roboto",Arial,sans-serif;font-weight:500;font-size:20px;color:var(--ink);letter-spacing:.5px}
.feature p{margin:10px auto 0;width:240px;font-size:13px;line-height:26px;color:var(--text)}

/* properties */
.properties-title{left:526px;top:1943px;font-size:102px}
.properties-tab{left:100px;top:2013px;width:380px;height:77px}
.properties-tab span{position:absolute;left:34px;top:20px;font-family:"Roboto",Arial,sans-serif;font-size:32px;color:var(--ink)}
.grid{left:100px;top:2090px;width:1000px;height:402px;display:grid;grid-template-columns:repeat(4,250px);grid-template-rows:repeat(2,201px)}
.tile{position:relative}
.tile-label{position:absolute;left:0;right:0;top:86px;text-align:center;font-family:"Roboto",Arial,sans-serif;font-size:22px;color:var(--white)}
.t1{background:linear-gradient(90deg,#e6e8ea 0%,#4e4e4e 30%,#e2e6ea 60%,#9fa6ab 100%)}
.t2{background:linear-gradient(180deg,#1e2a3e 0%,#17223a 50%,#1c2430 100%)}
.t3{background:linear-gradient(180deg,#3a7fd0 0%,#7fb3e6 40%,#c06a3a 55%,#3c6fa8 75%,#2d5b8c 100%)}
.t4{background:linear-gradient(180deg,#4a6e3a 0%,#2f5a2a 40%,#6fa04a 60%,#3e6f9a 85%,#2f5c80 100%)}
.t5{background:linear-gradient(180deg,#b7cbe0 0%,#3c5a38 40%,#4c4c46 60%,#6e9c3c 100%)}
.t6{background:linear-gradient(180deg,#6b8e4a 0%,#3a5e2e 35%,#e2e2e0 55%,#415f42 75%,#2d3d3a 100%)}
.t7{background:linear-gradient(180deg,#a9c2dc 0%,#d7dadc 35%,#6e7e56 60%,#8e8a80 100%)}
.t8{background:linear-gradient(180deg,#c9d8e6 0%,#5d7a5a 40%,#c0604a 60%,#2f4a5c 80%,#1f3446 100%)}

/* footer */
.site-footer{left:0;top:2733px;width:1200px;height:510px;background:var(--footer)}
.contact-card{left:140px;top:2603px;width:920px;height:263px;background:var(--white);box-shadow:0 1px 5px rgba(0,0,0,.2);text-align:center}
.contact-card h2{margin-top:50px;font-family:"Roboto",Arial,sans-serif;font-weight:400;font-size:34px;color:var(--ink)}
.contact-card p{margin-top:10px;font-style:italic;font-size:21px;color:var(--ink)}
.contact-input{left:117px;top:154px;width:548px;height:49px;border:1px solid #e2e2e2;font-size:12px;font-style:italic;color:var(--muted);padding:15px 16px;text-align:left}
.contact-send{left:665px;top:154px;width:138px;height:49px;background:var(--accent);color:var(--accent-text);font-family:"Roboto",Arial,sans-serif;font-weight:500;font-size:15px;letter-spacing:1px;line-height:49px}
.footer-nav{left:0;top:2904px;width:1200px;display:flex;justify-content:center;gap:26px;font-size:13px;color:var(--footer-text)}
.footer-brand{left:0;top:2962px;width:1200px;display:flex;justify-content:center;align-items:center;gap:10px;font-family:"Roboto",Arial,sans-serif;font-weight:500;font-size:24px;letter-spacing:1px;color:var(--footer-text)}
.footer-brand .brand-mark{background:var(--footer-text)}
.contact-item{width:300px;text-align:center;font-size:12px;line-height:22px;color:var(--footer-text)}
.contact-icon{width:54px;height:54px;border-radius:50%;background:#3b3b3b;margin:0 auto 16px;display:flex;align-items:center;justify-content:center}
.contact-icon.is-active{background:#e8e8e8}
.footer-rule{left:100px;top:3190px;width:1000px;height:1px;background:var(--line)}
.copyright{left:100px;top:3206px;font-size:12px;color:var(--footer-text)}
.social{right:100px;top:3207px;display:flex;gap:12px}
.social span{width:16px;height:16px;border-radius:50%;background:var(--footer-text)}
</style>
</head>
<body>

<header class="site-header abs">
  <div class="brand abs"><span class="brand-mark"></span>HARBOR CREST</div>
  <nav class="main-nav abs">
    <span>Home</span><span>Qeno Info</span><span>About Qe No Home</span><span>Downloads</span><span>Contact us</span>
  </nav>
</header>

<section class="hero abs" role="img" aria-label="Row of large suburban family homes with lawns beside a lake"></section>
<h1 class="hero-title abs">Harbor Crest Realty</h1>
<div class="search-input abs">Search Homes By City &amp; State,Zip Code</div>
<div class="search-btn abs">SEARCH</div>

<div class="about-main photo abs" role="img" aria-label="Modern home with deck and pool overlooking a lake and mountains"></div>
<h2 class="about-title ghost-title abs">ABOUT US</h2>
<p class="about-copy abs">Sed ut perspiciatis unde omnis iste natus error sit voluptatem accusantium doloremque laudantium, totam rem aperiam, eaque ipsa quae ab illo inventore veritatis et quasi architecto beatae vitae dicta sunt explicabo. Nemo enim ipsam voluptatem quia voluptas sit aspernatur aut odit aut fugit, sed quia tur magni dolores eos qui ratione voluptatem sequi nesciunt.</p>
<div class="read-more abs">READ MORE</div>
<div class="about-small-1 photo abs" role="img" aria-label="Lakeside deck with orange lounge chairs among trees"></div>
<div class="about-small-2 photo abs" role="img" aria-label="Lake house surrounded by tall palm trees"></div>

<h2 class="features-title ghost-title abs">FEATURES</h2>
<div class="features-photo photo abs" role="img" aria-label="Dark modern lake house among forest trees with lawn and stone edge"></div>

<div class="feature abs" style="left:105px;top:1690px">
  <svg width="40" height="40" viewBox="0 0 40 40"><circle cx="20" cy="20" r="16" fill="none" stroke="#8a8a8a" stroke-width="3.5"/><path d="M20 10v10h8" fill="none" stroke="#8a8a8a" stroke-width="3.5" stroke-linecap="round"/></svg>
  <h3>EFFICIENCY</h3>
  <p>At vero eos et accusamus et iusto odio dignissimos ducimus qui blanditiis praesentium</p>
</div>
<div class="feature abs" style="left:445px;top:1690px">
  <svg width="42" height="40" viewBox="0 0 42 40"><path d="M21 4 2 21h6v15h10V26h6v10h10V21h6z" fill="#8a8a8a"/></svg>
  <h3>PROPERTY LISTINGS</h3>
  <p>At vero eos et accusamus et iusto odio dignissimos ducimus qui blanditiis praesentium</p>
</div>
<div class="feature abs" style="left:793px;top:1690px">
  <svg width="46" height="40" viewBox="0 0 46 40"><circle cx="23" cy="11" r="7" fill="#8a8a8a"/><circle cx="9" cy="15" r="5" fill="#8a8a8a"/><circle cx="37" cy="15" r="5" fill="#8a8a8a"/><path d="M11 36c0-9 5-15 12-15s12 6 12 15z" fill="#8a8a8a"/><path d="M1 34c0-7 3-11 8-11 2 0 3 1 4 2-2 3-3 6-3 9z" fill="#8a8a8a"/><path d="M45 34c0-7-3-11-8-11-2 0-3 1-4 2 2 3 3 6 3 9z" fill="#8a8a8a"/></svg>
  <h3>EXPERTISE</h3>
  <p>At vero eos et accusamus et iusto odio dignissimos ducimus qui blanditiis praesentium</p>
</div>

<h2 class="properties-title ghost-title abs">PROPERTIES</h2>
<div class="properties-tab abs">
  <svg width="380" height="77" viewBox="0 0 380 77"><path d="M0 0H330L380 77H0z" fill="#c6d3e6"/></svg>
  <span>Our Properties</span>
</div>
<div class="grid abs">
  <div class="tile t1" role="img" aria-label="Glass-walled home interior opening to a lake view"></div>
  <div class="tile t2" role="img" aria-label="Lake house among pine trees at dusk"><span class="tile-label">Luxury Lake House</span></div>
  <div class="tile t3" role="img" aria-label="Orange lake house with boat dock on blue water"></div>
  <div class="tile t4" role="img" aria-label="Cottage with red roof on a green lakeshore"></div>
  <div class="tile t5" role="img" aria-label="Dark timber house on a green lawn"></div>
  <div class="tile t6" role="img" aria-label="White lake house behind trees with dock"></div>
  <div class="tile t7" role="img" aria-label="Covered porch with railing overlooking a lake"></div>
  <div class="tile t8" role="img" aria-label="Boathouses with red roofs on a lake"></div>
</div>

<footer class="site-footer abs"></footer>

<div class="contact-card abs">
  <h2>Want To Know More ?</h2>
  <p>Leave your feedback or request for direct contact here.</p>
  <div class="contact-input abs">Type Here</div>
  <div class="contact-send abs">SEND</div>
</div>

<nav class="footer-nav abs">
  <span>HOME</span><span>QENO INFO</span><span>ABOUT QE NO HOME</span><span>DOWNLOADS</span><span>CONTACT US</span>
</nav>
<div class="footer-brand abs"><span class="brand-mark"></span>HARBOR CREST</div>

<div class="contact-item abs" style="left:187px;top:3045px">
  <div class="contact-icon"><svg width="20" height="24" viewBox="0 0 20 24"><path d="M10 1a8 8 0 0 0-8 8c0 6 8 14 8 14s8-8 8-14a8 8 0 0 0-8-8z" fill="none" stroke="#b9b9b9" stroke-width="2"/><circle cx="10" cy="9" r="3" fill="none" stroke="#b9b9b9" stroke-width="2"/></svg></div>
  12 Lakeshore Drive, Suite 4,<br>Maple Bend, MN 55901
</div>
<div class="contact-item abs" style="left:462px;top:3045px">
  <div class="contact-icon is-active"><svg width="24" height="24" viewBox="0 0 24 24"><path d="M6 2l4 5-2 3c1 3 3 5 6 6l3-2 5 4-2 4c-9 0-18-9-18-18z" fill="none" stroke="#555" stroke-width="2" stroke-linejoin="round"/></svg></div>
  +1 555 014 2270
</div>
<div class="contact-item abs" style="left:737px;top:3045px">
  <div class="contact-icon"><svg width="24" height="18" viewBox="0 0 24 18"><rect x="1" y="1" width="22" height="16" fill="none" stroke="#b9b9b9" stroke-width="2"/><path d="M1 1l11 9 11-9" fill="none" stroke="#b9b9b9" stroke-width="2"/></svg></div>
  info@harborcrestrealty.com
</div>

<div class="footer-rule abs"></div>
<div class="copyright abs">© 2018 Copyrights Harbor Crest Realty All Rights Reserved</div>
<div class="social abs"><span></span><span></span></div>

</body>
</html>
```